furniture and home contents restoration

I need to list the services that we perform in our studio.
we serve the general public as well as the insurance/ remediation industry

```html
<!DOCTYPE html>
<html lang="en">
<head>
<meta charset="utf-8">
<title>Ashgrove Studio — Business Card</title>
<link href="https://fonts.googleapis.com/css2?family=PT+Serif:wght@400;700&display=swap" rel="stylesheet">
<style>
  :root {
    --ink: #1f2f38;
    --paper: #ffffff;
    --backdrop: #d6d6d6;
    --text-light: #f2f4f5;
  }
  * { box-sizing: border-box; margin: 0; padding: 0; }
  html, body { width: 1200px; height: 965px; overflow: hidden; }
  body {
    background: var(--backdrop);
    font-family: "PT Serif", Georgia, serif;
    position: relative;
  }
  .card {
    position: absolute;
    top: 159px;
    width: 383px;
    height: 669px;
    overflow: hidden;
  }
  .card--front { left: 186px; background: var(--paper); color: var(--ink); }
  .card--back { left: 653px; background: var(--ink); color: var(--text-light); }

  .brand {
    position: absolute;
    left: 0; right: 0;
    text-align: center;
    font-weight: 400;
    text-transform: uppercase;
    letter-spacing: 2px;
    white-space: nowrap;
    line-height: 1.2;
  }
  .card--front .brand { top: 82px; font-size: 28px; }
  .card--back .brand { top: 62px; font-size: 30px; }

  .front-body { position: absolute; left: 45px; width: 294px; }
  .holder { top: 317px; font-size: 26px; font-weight: 700; text-transform: uppercase; }
  .rule { position: absolute; height: 2px; background: var(--ink); }
  .card--front .rule { left: 45px; width: 294px; }

  .contact-list { list-style: none; font-size: 16px; line-height: 20px; }
  .contact-list li { display: flex; align-items: center; gap: 6px; white-space: nowrap; }
  .contact-list svg { width: 10px; height: 11px; fill: var(--ink); flex: none; }
  .phones { top: 386px; }
  .locations { top: 484px; }

  .tagline { top: 558px; font-size: 17px; line-height: 22px; }

  .service-band {
    position: absolute; top: 614px; left: 0; right: 0;
    display: flex; align-items: center; justify-content: space-between;
  }
  .service-band .bar { height: 13px; background: var(--ink); }
  .service-band .bar--left { width: 32px; }
  .service-band .bar--right { width: 38px; }
  .service-band span { font-size: 18px; text-transform: uppercase; letter-spacing: 0.2px; }

  .services {
    position: absolute; left: 34px; right: 10px;
    list-style: none; font-size: 14px; line-height: 17.8px;
    text-transform: uppercase;
  }
  .services li { white-space: nowrap; }
  .services li::before {
    content: ""; display: inline-block;
    width: 5px; height: 5px; border-radius: 50%;
    background: var(--text-light);
    margin-right: 5px; vertical-align: 2px;
  }
  .services--first { top: 170px; }
  .services--second { top: 377px; }
  .card--back .rule { left: 34px; width: 314px; top: 572px; background: var(--text-light); }
  .assessments {
    position: absolute; left: 34px; right: 30px; top: 592px;
    font-size: 12.5px; line-height: 16px; text-transform: uppercase;
  }
</style>
</head>
<body>
  <section class="card card--front">
    <h1 class="brand">Ashgrove Studio</h1>
    <h2 class="front-body holder">Daniel Moretti</h2>
    <div class="rule" style="top:365px"></div>
    <ul class="contact-list front-body phones">
      <li><svg viewBox="0 0 10 11"><path d="M2 0.5l2 2.2-1 1.3c.6 1.5 1.6 2.6 3 3.3l1.2-1 2.3 1.9-1.2 1.8C5 9.6 1 6 .5 1.8z"/></svg>555 201 4400</li>
      <li><svg viewBox="0 0 10 11"><path d="M2.5 0.5h5v10h-5zM3.5 1.5v7h3v-7zM4.5 9h1v.8h-1z" fill-rule="evenodd"/></svg>555 201 7832</li>
      <li><svg viewBox="0 0 10 11"><path d="M2.5 1h5v3h-5zM0.5 4.5h9v4h-1.5v2h-5v-2h-1.5zM3.5 7.5v2h3v-2z" fill-rule="evenodd"/></svg>555 201 4640</li>
    </ul>
    <div class="rule" style="top:464px"></div>
    <ul class="contact-list front-body locations">
      <li><svg viewBox="0 0 10 11"><path d="M0.5 2h9v7h-9zM1.5 3v.4l3.5 2.4 3.5-2.4V3zM1.5 4.6V8h7V4.6L5 7z" fill-rule="evenodd"/></svg>studio@ashgrovestudio.com</li>
      <li><svg viewBox="0 0 10 11"><path d="M5 0.5a3.6 3.6 0 0 1 3.6 3.6C8.6 6.6 5 10.5 5 10.5S1.4 6.6 1.4 4.1A3.6 3.6 0 0 1 5 .5zm0 2.2a1.4 1.4 0 1 0 0 2.8 1.4 1.4 0 0 0 0-2.8z" fill-rule="evenodd"/></svg>18 mill brook rd. riverton, ny 10000</li>
    </ul>
    <div class="rule" style="top:541px"></div>
    <p class="front-body tagline">serving the general public and the insurance industry for over 40 years</p>
    <div class="service-band">
      <div class="bar bar--left"></div>
      <span>Home Contents Restoration</span>
      <div class="bar bar--right"></div>
    </div>
  </section>

  <section class="card card--back">
    <h1 class="brand">Ashgrove Studio</h1>
    <ul class="services services--first">
      <li>Antique repair and restoration</li>
      <li>Art cleaning and remounting</li>
      <li>Art and mirror frame repair</li>
      <li>Chandelier cleaning and restoration</li>
      <li>Document restoration</li>
      <li>Glass, ceramic, and mirror repair</li>
      <li>Hardware repair and restoration</li>
      <li>Kitchen removal and reinstallation</li>
      <li>Lamp cleaning and restoration</li>
      <li>Lamp shade replacement</li>
    </ul>
    <ul class="services services--second">
      <li>Metal polishing and restoration</li>
      <li>Odor removal and ozone services</li>
      <li>Photo restoration</li>
      <li>Upholstery cleaning and deodorizing</li>
      <li>In-house upholstery and reupholstery</li>
      <li>Rug cleaning and restoration</li>
      <li>Musical instrument restoration</li>
      <li>Window treatment repair/ restoration</li>
      <li>Leather restoration and replacement</li>
      <li>Piano restoration and repair</li>
    </ul>
    <div class="rule"></div>
    <p class="assessments">On-site inspections and desk review services assessment reports and estimates for repair and restoration</p>
  </section>
</body>
</html>
```